Business Card Design Project - del varosi group

dear Sirs

we need business card design for our group ( DEL Varosi Group ) , i have got the Logo design of our group from pixel harbor in previous , so all need details relating to our group i think available with you, as well as the the chosen logo design

we hope to provide us with business card logo that to be appropaite and satisfactory to us .

thanks

note : logo design of our group is attached .
Updates

Reason: please extend the deadline of my project for additional 15 days because i didn't received appropriate design for our gruop yet . kindly beaware that i have received 77 design till now , supossed to send me 200-250 design at least . thanks

Target Market(s)

contents

name : Kerem EL Nadiri

position : Operation Manager

Industry/Entity Type

Business

Requirements
Must have

• person name

group logo
Nice to have
• logo color matching with back background

```html
<!DOCTYPE html>
<html lang="en">
<head>
<meta charset="utf-8">
<title>DEL Varosi Group – Business Card</title>
<link rel="stylesheet" href="https://fonts.googleapis.com/css2?family=Cinzel:wght@400;600&family=EB+Garamond:wght@400;500&display=swap">
<style>
  :root {
    --page: #e9ecef;
    --stripe-a: #3f7fae;
    --stripe-b: #4689ba;
    --stripe-c: #4f95c6;
    --sky: #4ba6e0;
    --ink: #060708;
    --ink-soft: #1a1c1f;
    --brand: #1d4f9a;
    --white: #ffffff;
    --muted: #8a8f96;
    --link: #4a9ee0;
    --ghost: #15171a;
  }
  * { box-sizing: border-box; margin: 0; padding: 0; }
  html, body { width: 1067px; height: 1200px; overflow: hidden; }
  body {
    background: var(--page);
    display: flex;
    align-items: center;
    justify-content: center;
    gap: 60px;
  }
  .card {
    position: relative;
    width: 440px;
    height: 580px;
    overflow: hidden;
    box-shadow: 0 10px 30px rgba(0,0,0,.18);
  }
  .card__art { position: absolute; inset: 0; }
  .brand {
    position: absolute;
    left: 0; right: 0;
    top: 110px;
    display: flex;
    align-items: center;
    justify-content: center;
    gap: 14px;
    font-family: "Cinzel", serif;
    font-weight: 600;
    font-size: 30px;
    letter-spacing: 1px;
    color: var(--brand);
  }
  .brand__mark { width: 22px; height: 22px; background: var(--brand); }
  .person {
    position: absolute;
    left: 0; right: 0;
    top: 318px;
    text-align: center;
    color: var(--white);
  }
  .person__name {
    font-family: "Cinzel", serif;
    font-weight: 400;
    font-size: 34px;
    letter-spacing: .5px;
  }
  .person__role {
    font-family: "EB Garamond", serif;
    font-size: 12px;
    letter-spacing: 1px;
    color: var(--muted);
    text-transform: uppercase;
    margin-top: 2px;
  }
  .person__rule {
    width: 170px; height: 3px;
    margin: 8px auto 18px;
    background: linear-gradient(90deg, transparent, var(--link), transparent);
  }
  .contact {
    list-style: none;
    font-family: "EB Garamond", serif;
    font-size: 15px;
    line-height: 1.55;
    text-transform: uppercase;
  }
  .contact__link { color: var(--link); }
  .ghost-name {
    position: absolute;
    left: 0; right: 0;
    top: 380px;
    text-align: center;
    font-family: "Cinzel", serif;
    font-weight: 600;
    font-size: 52px;
    line-height: 1.05;
    color: var(--ghost);
  }
</style>
</head>
<body>

<article class="card card--front">
  <svg class="card__art" viewBox="0 0 440 580" aria-hidden="true">
    <rect width="440" height="580" fill="var(--stripe-b)"/>
    <rect x="0" width="88" height="580" fill="var(--stripe-a)"/>
    <rect x="176" width="88" height="580" fill="var(--stripe-c)"/>
    <rect x="352" width="88" height="580" fill="var(--stripe-a)"/>
    <path d="M0 210 C 140 250, 300 270, 440 250 L440 330 L0 330 Z" fill="var(--sky)"/>
    <path d="M0 300 C 140 250, 300 235, 440 262 L440 580 L0 580 Z" fill="var(--ink)"/>
    <path d="M150 262 C 260 238, 360 240, 440 262 L440 300 C 360 275, 260 275, 150 262 Z" fill="var(--ink-soft)"/>
  </svg>
  <div class="brand"><span class="brand__mark"></span>DEL Varosi Group</div>
  <div class="person">
    <h1 class="person__name">Kerem EL Nadiri</h1>
    <p class="person__role">Operation Manager</p>
    <div class="person__rule"></div>
    <ul class="contact">
      <li>Phone: 0123 456 789</li>
      <li>Fax: 0123 456 789</li>
      <li class="contact__link">info@delvarosi.example</li>
      <li class="contact__link">www.delvarosi.example</li>
      <li>Po. Box: City Name, Etc.</li>
    </ul>
  </div>
</article>

<article class="card card--back">
  <svg class="card__art" viewBox="0 0 440 580" aria-hidden="true">
    <rect width="440" height="580" fill="var(--stripe-b)"/>
    <rect x="0" width="88" height="580" fill="var(--stripe-a)"/>
    <rect x="176" width="88" height="580" fill="var(--stripe-c)"/>
    <rect x="352" width="88" height="580" fill="var(--stripe-a)"/>
    <path d="M0 250 C 150 300, 300 300, 440 240 L440 360 L0 360 Z" fill="var(--sky)"/>
    <path d="M0 330 C 150 280, 300 235, 440 230 L440 580 L0 580 Z" fill="var(--ink)"/>
    <path d="M120 290 C 240 245, 340 232, 440 230 L440 270 C 340 262, 240 270, 120 290 Z" fill="var(--ink-soft)"/>
  </svg>
  <div class="brand"><span class="brand__mark"></span>DEL Varosi Group</div>
  <div class="ghost-name">DEL Varosi<br>Group</div>
</article>

</body>
</html>
```